Church Website with Home Page and Member Sermon Library

I am in need of an updated design for our church website. This will include 4 pages (outlined below). We are a conservative, evangelical, Christian church. The site should be modern and clean, while still reflecting our conservative values. I already have a logo for our church, and I want the site to incorporate the logo, and match the logo/branding. Stock photos are allowed if needed, but I have uploaded some images of our church and would prefer those images to be used if possible. Any stock photos used should not include any people in the photos (scenery, nature, buildings, animals, etc. are fine).

The site will need 4 pages: Home, Support Us (Donate), Login, and Recording Library.

Page 1: Home
The home page should include the following sections:

- Navigation: Should include links to each section of the home page plus a "listen live" link which will take the user to a live-streaming site and a "support us" link which will take the user to a support/donate page.

- Announcements: Can be either a banner or some other design, but there needs to be some way for us to post announcements for visitors to see. I'm open for creative ideas in this section, but would like it not to take up a lot of room on the page.

- About Us: Should include address, service times (see attached document), and information about the church.

- Pastor Bio: A section that introduces our pastor and gives a short bio about our pastor. Would like this section to include a picture of our pastor. Somewhere in this section I would like to include this Bible reference: "And I will give you pastors according to mine heart, which shall feed you with knowledge and understanding. Jer 3:15 LPW"

- Articles of Faith (What We Believe): This should include several sub-sections each with a heading, body, and possibly 1 or more scripture references. I have attached a document to the brief that includes our articles of faith. Feel free to be creative with this section in how you lay these out and format them.

- Support Us: A small section that explains what kind of support someone can give and a link to a donation page. The link can say something like "Support Us" or "Donate Now".

- Contact form: A contact form that allows the visitor to send us a message. The contact form should ask for name, email, phone, and message.

- Footer: A footer that will be displayed on all pages of the site. This should include at a minimum a link to the home page (or a link to each individual section in the home page if you prefer), a link to "listen live", a link to "support us", a link to "contact us" (or you can put the contact form directly in the footer if you prefer), the address, and a "member login" link.

Page 2: Support Us
The donation page should include a form the visitor can fill out to make a donation. We will embed a third party form later. For this design, please just mock out the design with a basic form asking for name, phone, and email.

Page 3: Login
The recording library (detailed below) will require members to login with a shared numeric code before accessing the page. We need a design for a login screen. The screen should include navigation/footer just like all other pages, but the body of the login page will consist only of a form that asks the user to enter the access code and then a "login" button.

Page 4: Recording Library

The library page is a member-only page that will require a shared, numeric pass code to access. On this page, members will be able to access a filterable list of past sermons. The page by default should display most recent sermons, but should also include a search form that allows the member to filter the sermon list to find a particular sermon. The search form should allow the user to select a filter type (e.g. Speaker name, date, event, etc.) and type in a value to search. They should be able to add multiple filters and remove filters that have been added. Each sermon that is displayed in the result list should include basic information such as title, date, speaker, tags, etc. along with a download icon, and an embedded audio player where they can click a play button to stream it on-demand. Each sermon should also have clickable tags associated with it that can be used to find related sermons.
Updates

I have uploaded several images of our church. Feel free to incorporate these into your design if possible.

Target Market(s)

Church Members

Industry/Entity Type

Religion

Number of Pages Required

4 page

Font styles to use
Sans Serif

Colors

Designer to choose colors to be used in the design.

Requirements
Must have
• Must incorporate the logo (attached)
Nice to have
• Would like the design to incorporate pictures of our church (attached) instead of stock photos if possible.
Should not have
• Please avoid an overly cluttered design. Stock photos used should not include any people in the photos.

```html
<!DOCTYPE html>
<html lang="en">
<head>
<meta charset="utf-8">
<title>Cedar Hill Chapel</title>
<link href="https://fonts.googleapis.com/css2?family=Cinzel:wght@400;600;700&family=Montserrat:wght@300;400;500;600;700&display=swap" rel="stylesheet">
<style>
:root{
  --green-dark:#3e6326;
  --green:#86ad6c;
  --green-soft:#8fb27a;
  --green-line:#b9d1a8;
  --blue:#29c1d7;
  --teal:#2bb3c6;
  --text:#4a4a4a;
  --white:#ffffff;
  --footer-bar:#eef0ea;
}
*{box-sizing:border-box;margin:0;padding:0}
html,body{width:1200px;height:4076px;overflow:hidden}
body{font-family:'Montserrat',sans-serif;color:var(--text);background:var(--white)}
.canvas{position:relative;width:1200px;height:4076px;overflow:hidden}
.abs{position:absolute}

/* header */
.site-header{position:absolute;left:0;top:0;width:1200px;height:76px;z-index:3}
.brand{position:absolute;left:133px;top:32px;display:flex;align-items:center;gap:8px;font-family:'Cinzel',serif;font-size:18px;font-weight:400;color:var(--teal);letter-spacing:.5px;white-space:nowrap;text-decoration:none}
.brand-mark{width:12px;height:12px;background:var(--teal);flex:none}
.main-nav a{position:absolute;top:37px;font-size:12.5px;color:#4d4d4d;text-decoration:none;font-weight:500;white-space:nowrap}
.nav-sep{position:absolute;top:36px;width:1px;height:14px;background:var(--teal)}
.pill{position:absolute;top:27px;height:35px;border-radius:18px;color:#fff;font-size:12.5px;font-weight:500;display:flex;align-items:center;justify-content:center;text-decoration:none}

/* hero */
.hero-photo{position:absolute;left:0;top:0;width:1200px;height:701px;background:linear-gradient(180deg,#ececec 0%,#d9d6d2 18%,#a88a74 40%,#8b6b56 52%,#b7b0a8 66%,#cfccc8 100%)}
.welcome-box{position:absolute;left:133px;top:438px;width:494px;height:168px;background:rgba(255,255,255,.85)}
.welcome-tag{position:absolute;left:171px;top:424px;width:174px;height:29px;background:var(--green);color:#fff;font-family:'Cinzel',serif;font-size:18px;letter-spacing:3px;display:flex;align-items:center;justify-content:center}
.hero-title{position:absolute;left:171px;top:470px;font-family:'Cinzel',serif;font-size:48px;line-height:54px;color:var(--green);font-weight:400;letter-spacing:1px}

/* announcement */
.announce{position:absolute;left:0;top:701px;width:1200px;height:113px;background:var(--green)}
.announce svg{position:absolute;left:0;top:0}
.announce-label{position:absolute;left:142px;top:38px;font-family:'Cinzel',serif;font-size:31px;letter-spacing:4px;color:#fff}
.announce-head{position:absolute;left:571px;top:35px;font-size:15px;font-weight:700;color:#fff}
.announce-sub{position:absolute;left:571px;top:59px;font-size:15px;color:#fff}

/* about */
.about-corner{position:absolute;left:122px;top:928px;width:163px;height:177px;background:var(--blue)}
.about-photo{position:absolute;left:131px;top:937px;width:455px;height:353px;background:linear-gradient(180deg,#e3e3e3 0%,#d6d4d2 35%,#9c7a63 55%,#a8a29b 72%,#c9c6c1 100%)}
.about-accent{position:absolute;left:1004px;top:1222px;width:117px;height:135px;background:var(--green)}
.about-box{position:absolute;left:481px;top:882px;width:630px;height:464px;border:1.5px solid #8fd7e3;background:#fff}
.section-title{font-family:'Cinzel',serif;font-weight:700;color:var(--green-dark)}
.about-title{position:absolute;left:638px;top:952px;font-size:35px}
.rule{position:absolute;height:2px}
.about-text{position:absolute;left:638px;top:1022px;width:405px;font-size:13.5px;line-height:23px;color:#555}
.about-text p{margin-bottom:8px}
.timing-label{position:absolute;left:638px;top:1195px;font-size:15px;font-weight:600;color:var(--green)}
.timing{position:absolute;font-size:11.5px;font-weight:600;color:#333;white-space:nowrap}

/* pastor */
.pastor-band{position:absolute;left:0;top:1425px;width:1200px;height:557px;background:var(--blue)}
.pastor-title{position:absolute;left:0;width:1200px;top:1483px;text-align:center;font-size:38px;color:#fff}
.pastor-text{position:absolute;left:133px;top:1618px;width:470px;font-size:15px;line-height:23.5px;color:#fff}
.pastor-text p{margin-bottom:6px}
.quote{position:absolute;left:136px;top:1792px;width:462px;height:110px;background:var(--green-dark);border-radius:26px 0 26px 0;padding:16px 30px 0 40px;color:#fff}
.quote em{display:block;font-size:12.5px;line-height:19px;font-weight:500}
.quote strong{display:block;margin-top:8px;font-size:13.5px;font-weight:600}
.pastor-frame{position:absolute;left:647px;top:1599px;width:417px;height:419px;border:2px solid #9ae4ee}
.pastor-photo{position:absolute;left:662px;top:1613px;width:391px;height:396px;background:linear-gradient(160deg,#6d5a48 0%,#3a332e 40%,#1c1c1e 70%,#4c4038 100%)}
.pastor-corner{position:absolute;left:929px;top:2009px;width:135px;height:9px;background:var(--teal)}

/* articles */
.articles-title{position:absolute;left:0;width:1200px;top:2100px;text-align:center;font-size:41px}
.card{position:absolute;border:1.5px solid var(--green-line);background:#fff}
.card h3{position:absolute;left:36px;font-family:'Montserrat',sans-serif;font-weight:400;font-size:20px;letter-spacing:3px;color:var(--green-dark);white-space:nowrap}
.card .bar{position:absolute;left:0;width:3px;height:34px;background:var(--green-dark)}
.card .body{position:absolute;left:36px;right:10px;font-size:13px;line-height:25.5px;color:#555}
.card .body.small{font-size:12.4px;line-height:25.5px}
.card .body p{margin-bottom:6px}

/* donate */
.donate{position:absolute;left:0;top:3150px;width:1200px;height:481px;background:var(--green-soft)}
.donate-title{position:absolute;left:138px;top:3238px;font-size:41px;color:#fff}
.donate-text{position:absolute;left:138px;top:3325px;width:430px;font-size:16px;line-height:29px;color:#fff}
.checks{position:absolute;left:636px;top:3314px;list-style:none}
.checks li{display:flex;align-items:center;gap:10px;height:35px;font-size:17px;color:#fff;font-weight:500;white-space:nowrap}
.donate-btn{position:absolute;left:633px;top:3435px;width:181px;height:46px;border:2px solid #fff;border-radius:24px;color:#fff;font-size:13px;font-weight:700;display:flex;align-items:center;justify-content:center;text-decoration:none}

/* footer */
.footer-brand{position:absolute;left:128px;top:3800px;display:flex;align-items:center;gap:8px;font-family:'Cinzel',serif;font-size:17px;color:var(--teal);white-space:nowrap}
.footer-div{position:absolute;top:3631px;width:1px;height:365px;background:#e6e6e6}
.footer-tick{position:absolute;top:3706px;width:2px;height:22px;background:var(--teal)}
.footer-head{position:absolute;top:3706px;font-size:14px;letter-spacing:2.5px;color:var(--green-dark)}
.footer-links a{position:absolute;left:400px;font-size:13.5px;color:#555;text-decoration:none}
.field{position:absolute;left:597px;width:217px;border:1.5px solid #cfcfcf;font-size:10.5px;color:#888;padding:9px 12px}
.small-btn{position:absolute;height:31px;border-radius:16px;color:#fff;font-size:10.5px;font-weight:600;display:flex;align-items:center;justify-content:center;text-decoration:none}
.address{position:absolute;left:913px;top:3746px;font-size:12px;line-height:17px;color:#333;font-style:normal}
.copyright{position:absolute;left:0;top:4021px;width:1200px;height:55px;background:var(--footer-bar);display:flex;align-items:center;justify-content:center;font-size:12.5px;color:#666}
</style>
</head>
<body>
<div class="canvas">

  <!-- Hero -->
  <div class="hero-photo" role="img" aria-label="Brick church building with pitched roof under a grey sky"></div>

  <header class="site-header">
    <a class="brand"><span class="brand-mark"></span>Cedar Hill Chapel</a>
    <nav class="main-nav">
      <a style="left:374px">ABOUT US</a>
      <span class="nav-sep" style="left:461px"></span>
      <a style="left:483px">PASTOR BIO</a>
      <span class="nav-sep" style="left:583px"></span>
      <a style="left:605px">ARTICLES OF FAITH</a>
      <span class="nav-sep" style="left:743px"></span>
      <a style="left:763px">CONTACT</a>
    </nav>
    <a class="pill" style="left:855px;width:120px;background:var(--green)">LISTEN LIVE</a>
    <a class="pill" style="left:981px;width:120px;background:var(--blue)">SUPPORT US</a>
  </header>

  <div class="welcome-box"></div>
  <div class="welcome-tag">WELCOME TO</div>
  <h1 class="hero-title">CEDAR HILL<br>CHAPEL</h1>

  <!-- Announcement -->
  <section class="announce">
    <svg width="1200" height="113" viewBox="0 0 1200 113"><polygon points="0,0 540,0 480,113 0,113" fill="var(--green-dark)"/></svg>
    <div class="announce-label">ANNOUNCEMENT</div>
    <div class="announce-head">LOREM IPSUM DOLOR SIT AMET CONSECTETUR ADIPISCING</div>
    <div class="announce-sub">Ut enim ad minim veniam quis nostrud exercitatio</div>
  </section>

  <!-- About -->
  <div class="about-corner"></div>
  <div class="about-accent"></div>
  <div class="about-box"></div>
  <div class="about-photo" role="img" aria-label="Side view of the brick church and its parking lot"></div>
  <h2 class="section-title about-title">ABOUT OUR CHURCH</h2>
  <div class="rule" style="left:638px;top:1002px;width:88px;background:var(--green-dark)"></div>
  <div class="about-text">
    <p>Lorem ipsum dolor sit amet, consectetur adipiscing elit, sed do eiusmod tempor incididunt ut labore et dolore magna aliqua. Ut enim ad minim veniam, quis nostrud exercitation</p>
    <p>Allamco laboris nisi ut aliquip ex ea commodo consequat. Duis aute irure dolor in reprehenderit in voluptate velit esse cillum dolore eu fugiat nulla pariatur.</p>
  </div>
  <div class="timing-label">SERVICE TIMING:</div>
  <div class="timing" style="left:638px;top:1231px">Wednesday Night Service: 7:30 PM</div>
  <div class="timing" style="left:858px;top:1233px">Sunday Morning Service: 11:00 AM</div>
  <div class="timing" style="left:638px;top:1259px">Sunday School: 10:00 AM</div>
  <div class="timing" style="left:858px;top:1260px">Sunday Night Service: 5:30 PM</div>

  <!-- Pastor -->
  <section class="pastor-band" role="img" aria-label="Church building tinted in blue behind the pastor section"></section>
  <h2 class="section-title pastor-title" style="color:#fff">OUR PASTOR</h2>
  <div class="rule" style="left:546px;top:1545px;width:98px;background:#fff"></div>
  <div class="pastor-text">
    <p>Lorem ipsum dolor sit amet, consectetur adipiscing elit, sed do eiusmod tempor incididunt ut labore et dolore magna aliqua. Ut enim ad minim veniam, quis nostrud exercitation</p>
    <p>Allamco laboris nisi ut aliquip ex ea commodo consequat. Duis aute irure dolor in reprehenderit in voluptate velit esse ea commodo consequat. Duis aute irure dolor in</p>
  </div>
  <blockquote class="quote">
    <em>“And I will give you pastors according to mine heart, which shall feed you with knowledge and understanding”</em>
    <strong>Jer 3:15 LPW</strong>
  </blockquote>
  <div class="pastor-frame"></div>
  <div class="pastor-photo" role="img" aria-label="Portrait of the pastor holding an open Bible inside the sanctuary"></div>
  <div class="pastor-corner"></div>

  <!-- Articles of faith -->
  <h2 class="section-title articles-title">ARTICLES OF FAITH</h2>
  <div class="rule" style="left:557px;top:2158px;width:86px;background:var(--green-dark)"></div>

  <article class="card" style="left:141px;top:2213px;width:466px;height:260px">
    <span class="bar" style="top:43px"></span>
    <h3 style="top:47px">THE GOD HEAD.</h3>
    <div class="body" style="top:86px">We believe in the God head bodily, known as the Divine Trinity. This body consist of God the father, Jesus Christ, his only begotten son and the redeemer of the world, and of the Holy Ghost, The third person of the Divine Trinity.</div>
  </article>

  <article class="card" style="left:619px;top:2213px;width:466px;height:260px">
    <span class="bar" style="top:43px"></span>
    <h3 style="top:47px">BAPTISM OF THE HOLY GHOST</h3>
    <div class="body" style="top:86px">We believe in the baptism of the Holy Ghost as it is taught in the Bible and promised by our Lord Jesus Christ, with speaking in tongues as the Spirit gives utterance as the initial evidence. Acts 2:4 we believe that the gift of the Holy Ghost is for all believers as the Lord promised. Acts 2:17-1</div>
  </article>

  <article class="card" style="left:141px;top:2487px;width:466px;height:396px">
    <span class="bar" style="top:36px"></span>
    <h3 style="top:40px">FULL SALVATION</h3>
    <div class="body small" style="top:76px">
      <p>We believe that Salvation is received only when a person comes to the realization that he or she is lost and separated from God and becomes full of godly sorrow, confessing their sins and true repentance, believing in the shed blood of the Lord Jesus Christ as the only sacrifice for sins. Through the blood of Christ we have:</p>
      <p style="margin-top:10px;line-height:27.5px">(1) remission of sins, Matthew 26:28 Heb 9:22<br>(2) Sanctification. Hebrews 13:12<br>(3) redemption. Revelations 5:9<br>(4) cleansing. 1 John 1:7 Rev. 1:5<br>(5). Justification. Romans 5:9</p>
    </div>
  </article>

  <article class="card" style="left:619px;top:2487px;width:466px;height:158px">
    <span class="bar" style="top:28px"></span>
    <h3 style="top:32px">DIVINE HEALING</h3>
    <div class="body" style="top:66px">We believe Divine Healing to be included in the atonement of Jesus Christ our Lord, And believe that it is still for us today. 1 Peter 2:24 Luke 9:1-2 Mark 16-18 James 5:15</div>
  </article>

  <article class="card" style="left:619px;top:2663px;width:466px;height:157px">
    <span class="bar" style="top:37px"></span>
    <h3 style="top:41px">SECOND COMING OF CHRIST</h3>
    <div class="body" style="top:75px">We believe in the second coming of Jesus Christ. Matthew 24:44 Luke 12:40</div>
  </article>

  <article class="card" style="left:621px;top:2840px;width:466px;height:215px">
    <span class="bar" style="top:38px"></span>
    <h3 style="top:42px">SANCTIFICATION</h3>
    <div class="body" style="top:76px"><p>“Sanctify them through thy truth thy word is truth St John 17:17. For this is the will of God even your sanctification”</p><p>We believe in a set apart life, separate from the world to Christ 2 Cor 6:17-18</p></div>
  </article>

  <article class="card" style="left:143px;top:2897px;width:466px;height:158px">
    <span class="bar" style="top:38px"></span>
    <h3 style="top:42px">ETERNITY</h3>
    <div class="body" style="top:76px;right:6px;font-size:12.8px">We believe in Literal Eternity. Eternal Life for the believer and eternal death for those without Christ. Revelations 21:1-27</div>
  </article>

  <!-- Donate -->
  <section class="donate" role="img" aria-label="Church building tinted in green behind the donation section"></section>
  <h2 class="section-title donate-title" style="color:#fff">DONATE US</h2>
  <p class="donate-text">Lorem ipsum dolor sit amet, consectetur adipiscing elit, sed do eiusmod tempor incididunt ut labore et dolore magna aliqua. Ut enim ad minim Lorem ipsum dolor sit amet, consectetur adipiscinnim ad minim Lorem ipsum dolor sit ipsum dolor sit amet, consectetur</p>
  <ul class="checks">
    <li><svg width="20" height="16" viewBox="0 0 20 16"><path d="M2 8l6 6L18 2" fill="none" stroke="#fff" stroke-width="3" stroke-linecap="round" stroke-linejoin="round"/></svg>Consectetur adipiscing elit, sed do</li>
    <li><svg width="20" height="16" viewBox="0 0 20 16"><path d="M2 8l6 6L18 2" fill="none" stroke="#fff" stroke-width="3" stroke-linecap="round" stroke-linejoin="round"/></svg>Eiusmod tempor incididunt ut labore et dolore</li>
    <li><svg width="20" height="16" viewBox="0 0 20 16"><path d="M2 8l6 6L18 2" fill="none" stroke="#fff" stroke-width="3" stroke-linecap="round" stroke-linejoin="round"/></svg>Magna aliqua Ut enim ad minim</li>
  </ul>
  <a class="donate-btn">DONATE NOW</a>

  <!-- Footer -->
  <footer>
    <div class="footer-brand"><span class="brand-mark"></span>Cedar Hill Chapel</div>
    <span class="footer-div" style="left:372px"></span>
    <span class="footer-div" style="left:571px"></span>
    <span class="footer-div" style="left:842px"></span>

    <span class="footer-tick" style="left:372px"></span>
    <div class="footer-head" style="left:397px">NAVIGATION</div>
    <nav class="footer-links">
      <a style="top:3742px">home</a>
      <a style="top:3772px">Hbout Us</a>
      <a style="top:3802px">Paster Bio</a>
      <a style="top:3832px">Article of Faith</a>
      <a style="top:3862px">Listen Live</a>
      <a style="top:3892px">Contact Us</a>
    </nav>

    <span class="footer-tick" style="left:571px"></span>
    <div class="footer-head" style="left:594px">GET IN TOUCH</div>
    <div class="field" style="top:3744px;height:33px">Name</div>
    <div class="field" style="top:3785px;height:33px">Email address</div>
    <div class="field" style="top:3824px;height:33px">Phone number</div>
    <div class="field" style="top:3866px;height:56px">Message</div>
    <a class="small-btn" style="left:594px;top:3935px;width:133px;background:var(--green)">SUBMIT NOW</a>

    <span class="footer-tick" style="left:842px"></span>
    <div class="footer-head" style="left:872px">CONTACT US</div>
    <svg class="abs" style="left:869px;top:3745px" width="30" height="30" viewBox="0 0 30 30"><circle cx="15" cy="15" r="15" fill="var(--green)"/><path d="M15 7a5.5 5.5 0 0 0-5.5 5.5c0 4 5.5 10 5.5 10s5.5-6 5.5-10A5.5 5.5 0 0 0 15 7z" fill="#fff"/><circle cx="15" cy="12.5" r="2" fill="var(--green)"/></svg>
    <address class="address">88 Meadow Lane, Suite<br>210, Fairview,<br>OH 44120 USA</address>
    <a class="small-btn" style="left:877px;top:3817px;width:134px;background:var(--green)">DONATE NOW</a>
    <a class="small-btn" style="left:875px;top:3858px;width:134px;background:var(--blue)">MEMBER LOGIN</a>
  </footer>

  <div class="copyright">© 2023 Cedar Hill Chapel. All Rights Reserved</div>
</div>
</body>
</html>
```